Bundrova Hero Unit Icon

Bundrova (http://www.bundrova-example.com) is a "software as a service" site that lets developers create Zip files on the fly so they don't have to stress their servers. The site design is pretty much done, but I need an image to replace the one at the top of the main page, to the right of "Create Zip Files Instantly" (currently just a browser that says Spindle Harbor. It will be replaced with your image).

The new image should somehow illustrate that you can quickly Zip up any type of file (images, documents, binary files) and the output is a Zip file that is instantly ready to download.

Target Market(s)

Software developers

Industry/Entity Type

Software

Requirements
Must have
• Must work well when placed in the existing hero unit space with the green background.

Must scale well (max size is 570 x 365). The design is responsive.

```html
<!DOCTYPE html>
<html lang="en">
<head>
<meta charset="utf-8">
<title>Bundrova — Create Zip Files Instantly</title>
<link rel="stylesheet" href="https://fonts.googleapis.com/css2?family=Open+Sans:wght@400;600;700&display=swap">
<style>
  :root {
    --canvas-bg: #e9e9e9;
    --header-bg: #2e2e2e;
    --header-bg-dark: #262626;
    --nav-active-bg: #333333;
    --nav-text: #ffffff;
    --brand-text: #d8d8d8;
    --brand-green: #7a9d3f;
    --hero-green: #7d9f41;
    --accent-green: #8db04c;
    --hero-art-dark: #242424;
    --hero-art-mid: #3a3a3a;
    --hero-rule: #3c3c3c;
    --button-dark: #2f2f2f;
    --button-light: #f4f4f4;
    --text-dark: #333333;
    --text-body: #555555;
    --link-blue: #2a7ab8;
    --page-bg: #ffffff;
    --icon-ring: #3a3a3a;
    --demo-border: #dddddd;
  }
  * { box-sizing: border-box; margin: 0; padding: 0; }
  html, body {
    width: 1200px; height: 851px; overflow: hidden;
    background: var(--canvas-bg);
    font-family: "Open Sans", Arial, sans-serif;
    color: var(--text-body);
  }
  .page {
    position: absolute; left: 0; top: 34px;
    width: 1200px; height: 817px; overflow: hidden;
    background: var(--page-bg);
  }

  /* Header */
  .site-header {
    position: absolute; left: 0; top: 0; width: 1200px; height: 65px;
    background: linear-gradient(var(--header-bg), var(--header-bg-dark));
  }
  .brand {
    position: absolute; left: 44px; top: 19px;
    display: flex; align-items: center; gap: 10px;
  }
  .brand-mark { width: 26px; height: 26px; background: var(--brand-green); border-radius: 3px; }
  .brand-name { font-size: 23px; font-weight: 400; color: var(--brand-text); line-height: 26px; }
  .main-nav { position: absolute; top: 13px; left: 0; }
  .main-nav a {
    position: absolute; top: 0; height: 38px; line-height: 38px;
    font-size: 14px; font-weight: 600; color: var(--nav-text); text-decoration: none;
    white-space: nowrap;
  }
  .main-nav a.is-active {
    color: var(--accent-green); background: var(--nav-active-bg);
    padding: 0 15px;
  }

  /* Hero */
  .hero {
    position: absolute; left: 0; top: 65px; width: 1200px; height: 371px;
    background: var(--hero-green);
  }
  .hero-title {
    position: absolute; left: 44px; top: 40px;
    font-size: 35px; font-weight: 600; color: #ffffff; letter-spacing: -0.2px;
    line-height: 48px; white-space: nowrap;
    text-shadow: 0 1px 2px rgba(0,0,0,0.25);
  }
  .hero-copy {
    position: absolute; left: 44px; top: 112px; width: 540px;
    font-size: 14.5px; line-height: 28px; color: #ffffff;
  }
  .hero-copy p + p { margin-top: 24px; }
  .hero-actions { position: absolute; left: 44px; top: 277px; display: flex; gap: 13px; }
  .btn {
    display: block; height: 46px; line-height: 46px; padding: 0; border-radius: 3px;
    font-size: 17px; font-weight: 600; text-decoration: none;
    text-align: center; white-space: nowrap;
  }
  .btn-primary { background: var(--button-dark); color: #ffffff; width: 98px; }
  .btn-secondary { background: var(--button-light); color: var(--text-dark); width: 131px; font-weight: 400; }
  .hero-art {
    position: absolute; left: 607px; top: 29px; width: 534px; height: 342px;
    background: radial-gradient(ellipse at 45% 40%, var(--hero-art-mid), var(--hero-art-dark) 75%);
  }
  .hero-rule {
    position: absolute; left: 44px; top: 436px; width: 1097px; height: 3px;
    background: var(--hero-rule);
  }

  /* Sections */
  .section-title {
    position: absolute; left: 44px;
    font-size: 29px; font-weight: 600; color: var(--text-dark); white-space: nowrap;
  }
  .section-title .brace { color: var(--brand-green); font-weight: 400; }
  .highlights-title { top: 486px; }
  .try-title { top: 712px; }

  .highlight { position: absolute; top: 563px; width: 350px; }
  .highlight-icon { position: absolute; left: 0; top: 0; width: 46px; height: 46px; }
  .highlight-body { position: absolute; left: 64px; top: 15px; width: 285px; }
  .highlight h3 { font-size: 12.5px; font-weight: 600; color: var(--text-dark); margin-bottom: 9px; }
  .highlight p { font-size: 12.2px; line-height: 21px; color: var(--text-body); }
  .highlight a { color: var(--link-blue); text-decoration: none; }

  .try-copy { position: absolute; left: 44px; top: 774px; font-size: 12.2px; color: var(--text-dark); white-space: nowrap; }
  .demo-frame {
    position: absolute; left: 44px; top: 815px; width: 1097px; height: 60px;
    border: 1px solid var(--demo-border);
  }
</style>
</head>
<body>
<div class="page">
  <header class="site-header">
    <div class="brand">
      <span class="brand-mark"></span>
      <span class="brand-name">Bundrova</span>
    </div>
    <nav class="main-nav">
      <a class="is-active" href="#" style="left:730px">Home</a>
      <a href="#" style="left:811px">Docs</a>
      <a href="#" style="left:870px">Plans</a>
      <a href="#" style="left:933px">Blog</a>
      <a href="#" style="left:989px">Contact Us</a>
      <a href="#" style="left:1087px">Log In</a>
    </nav>
  </header>

  <section class="hero">
    <h1 class="hero-title">Create Zip Files Instantly</h1>
    <div class="hero-copy">
      <p>Use our API to create zip files from existing online files and let your users download them immediately. No more tying up your servers generating zip files or making your users download multiple files one at a time.</p>
      <p>Save yourself and your users the headaches. Bundle it, Bundrova!</p>
    </div>
    <div class="hero-actions">
      <a class="btn btn-primary" href="#">Sign Up</a>
      <a class="btn btn-secondary" href="#">See a Demo</a>
    </div>
    <div class="hero-art" role="img" aria-label="Illustration of documents, photos, folders and a disc flying into a green zip file with a Download Now button"></div>
  </section>
  <div class="hero-rule"></div>

  <h2 class="section-title highlights-title"><span class="brace">{</span> Highlights <span class="brace">}</span></h2>

  <div class="highlight" style="left:44px">
    <svg class="highlight-icon" viewBox="0 0 46 46" aria-hidden="true">
      <circle cx="23" cy="23" r="21" fill="#fff" stroke="var(--icon-ring)" stroke-width="3"/>
      <circle cx="23" cy="23" r="16" fill="var(--icon-ring)"/>
      <circle cx="23" cy="23" r="7" fill="none" stroke="var(--accent-green)" stroke-width="2"/>
      <path d="M23 19v4h3" fill="none" stroke="var(--accent-green)" stroke-width="2"/>
    </svg>
    <div class="highlight-body">
      <h3>Ready Instantly</h3>
      <p>Your Zip file is ready for delivery as soon as you send us the file list via our API, no matter how big it is or how many files it includes. <a href="#">Try it</a>.</p>
    </div>
  </div>

  <div class="highlight" style="left:419px">
    <svg class="highlight-icon" viewBox="0 0 46 46" aria-hidden="true">
      <circle cx="23" cy="23" r="21" fill="#fff" stroke="var(--icon-ring)" stroke-width="3"/>
      <circle cx="23" cy="23" r="16" fill="var(--icon-ring)"/>
      <path d="M16 30l12-12" stroke="var(--accent-green)" stroke-width="3" stroke-linecap="round"/>
      <path d="M30 14v4M28 16h4M33 20v2M32 21h2" stroke="var(--accent-green)" stroke-width="1.5"/>
    </svg>
    <div class="highlight-body">
      <h3>Simple Integration</h3>
      <p>Our API, based on REST and JSON, is as simple as they come. Plus, we have <a href="#">great documentation</a>.</p>
    </div>
  </div>

  <div class="highlight" style="left:794px">
    <svg class="highlight-icon" viewBox="0 0 46 46" aria-hidden="true">
      <circle cx="23" cy="23" r="21" fill="#fff" stroke="var(--icon-ring)" stroke-width="3"/>
      <circle cx="23" cy="23" r="16" fill="var(--icon-ring)"/>
      <circle cx="23" cy="23" r="7" fill="none" stroke="var(--accent-green)" stroke-width="2"/>
      <path d="M23 19v7M20 23l3 3 3-3" fill="none" stroke="var(--accent-green)" stroke-width="2"/>
    </svg>
    <div class="highlight-body">
      <h3>Lots of Space</h3>
      <p>Our plans range from 1,000 to 250,000 Zip files. Need unlimited downloads? We got that. Check out our <a href="#">plans.</a></p>
    </div>
  </div>

  <h2 class="section-title try-title"><span class="brace">{</span> Try It <span class="brace">}</span></h2>
  <p class="try-copy">The demo below lets a user instantly download a custom Zip file containing just the images they want. Try it out, then check out the code behind it.</p>
  <div class="demo-frame"></div>
</div>
</body>
</html>
```